Tidal Forge - Crypto Currency Miner Powered by Renewable Energy Website

We Need Web Pages Design for Website for Crypto Currency Miner

Serivices include:
Mining Rig Sales
Housing for Rigs turnkey on renewable energy grid
Cloud Mining term packages
Updates

http://www.vaultrigsurvey.example (Competitors sites)

Target Market(s)

Investers for Mining Rigs and terms for 1,2 or 3 years of Hash rate

Industry/Entity Type

Mining

Number of Pages Required

5+ page

Font styles to use
Sans Serif

Colors
add136
9bcb3c
606060
474747
ffc214
cadf82
fbee3e
876aae
6b449b

Requirements
Must have
• Pictures of Solar, Wind and power Factor Correction units
Nice to have
• e-commerce platform so contract terms can be purchased through website
Should not have
• Heavy construction equipment

```html
<!DOCTYPE html>
<html lang="en">
<head>
<meta charset="utf-8">
<title>Tidal Forge – Renewable Crypto Mining</title>
<link rel="stylesheet" href="https://fonts.googleapis.com/css2?family=Montserrat:wght@600;700&family=Open+Sans:wght@400;600;700&display=swap">
<style>
:root{
  --green:#2e9e44;
  --green-dark:#1f7f33;
  --green-light:#7cc242;
  --ink:#474747;
  --grey:#606060;
  --panel:#ebebeb;
  --dark:#4d4d4d;
  --footer:#8e8e8e;
  --white:#ffffff;
}
*{margin:0;padding:0;box-sizing:border-box}
html,body{width:1200px;height:3822px;overflow:hidden}
body{font-family:"Open Sans",Arial,sans-serif;color:var(--ink);background:var(--white)}
.page{position:relative;width:1200px;height:3822px}
section,header,footer{position:absolute;left:0;width:1200px}

/* header */
.site-header{top:0;height:158px;background:var(--white);border-top:8px solid var(--grey)}
.brand{position:absolute;left:112px;top:30px;display:flex;align-items:center;gap:14px}
.brand-dot{width:44px;height:44px;border-radius:50%;background:var(--green)}
.brand-name{font-family:"Open Sans",sans-serif;font-weight:700;font-size:34px;color:var(--grey)}
.call{position:absolute;left:730px;top:30px;text-align:center}
.call-label{font-family:"Montserrat",sans-serif;font-weight:700;font-size:20px;color:var(--ink);letter-spacing:.5px}
.call-number{display:flex;align-items:center;gap:8px;margin-top:6px;font-weight:700;font-size:22px;color:var(--ink)}
.follow{position:absolute;left:982px;top:22px;text-align:center}
.follow-label{font-family:"Montserrat",sans-serif;font-weight:700;font-size:20px;color:var(--ink)}
.follow-icons{display:flex;gap:8px;margin-top:10px}
.follow-icons span{width:30px;height:30px;background:var(--green);border-radius:3px}
.main-nav{position:absolute;left:466px;top:104px;width:734px;height:42px;background:var(--green);clip-path:polygon(30px 0,100% 0,100% 100%,0 100%);display:flex;align-items:center;padding-left:64px}
.main-nav a{color:var(--white);text-decoration:none;font-size:17px;font-weight:600;display:flex;align-items:center}
.main-nav a+a::before{content:"";width:12px;height:6px;border-top:2px solid rgba(255,255,255,.7);border-bottom:2px solid rgba(255,255,255,.7);margin:0 14px}
.main-nav a.active span{border-bottom:2px solid var(--white)}

/* hero */
.hero{top:158px;height:700px;overflow:hidden}
.hero-visual{position:absolute;inset:0;
  background:
    radial-gradient(ellipse 420px 200px at 600px 470px,rgba(255,236,170,.95),rgba(255,200,90,.55) 45%,rgba(255,170,60,0) 100%),
    linear-gradient(180deg,#233650 0%,#4d5a72 22%,#a68a66 42%,#e3a553 56%,#2c3a48 64%,#23313d 78%,#4c7a34 90%,#5f8f3c 100%)}
.hero-title{position:absolute;top:325px;width:100%;text-align:center;font-family:"Montserrat",sans-serif;font-weight:700;color:var(--white);font-size:44px;line-height:56px;letter-spacing:1px}
.hero-arrow{position:absolute;top:392px}

/* section titles */
.section-title{position:absolute;width:100%;text-align:center;font-family:"Open Sans",sans-serif;font-weight:700;font-size:31px;display:flex;justify-content:center;align-items:center;gap:10px}
.section-title::after{content:"";position:absolute;left:585px;top:54px;width:30px;height:2px;background:currentColor;opacity:.5}

/* about */
.about{top:858px;height:543px;background:var(--panel)}
.about .section-title{top:88px;color:var(--grey)}
.about-photo{position:absolute;left:115px;top:182px;width:323px;height:216px;
  background:
    radial-gradient(ellipse 110px 80px at 190px 70px,rgba(255,200,110,.9),rgba(230,140,50,.4) 55%,rgba(0,0,0,0) 100%),
    linear-gradient(180deg,#2a2522 0%,#5a3a22 45%,#8a6540 70%,#3c3a38 100%)}
.about-text{position:absolute;left:484px;top:184px;width:700px;font-size:13.5px;line-height:22px;color:var(--grey)}
.about-text p+p{margin-top:14px}
.read-more{position:absolute;left:489px;top:364px;width:136px;height:34px;border-radius:17px;background:var(--green);color:var(--white);font-size:11px;font-weight:700;display:flex;align-items:center;padding-left:22px;gap:14px}
.read-more i{width:24px;height:24px;border-radius:50%;background:var(--white);display:flex;align-items:center;justify-content:center}

/* services */
.services{top:1401px;height:811px;background:
  radial-gradient(ellipse 500px 300px at 1000px 120px,rgba(150,200,120,.35),rgba(150,200,120,0)),
  linear-gradient(180deg,#3a9f4a,#2a8d3c 60%,#1f8032)}
.services .section-title{top:54px;color:var(--white)}
.service-card{position:absolute;width:216px;height:271px;background:var(--white);text-align:center;padding-top:26px}
.service-icon{width:90px;height:90px;border-radius:50%;border:3px solid var(--green);margin:0 auto;padding:5px}
.service-icon svg{display:block;width:100%;height:100%}
.service-card h3{font-family:"Open Sans",sans-serif;font-weight:700;font-size:15px;line-height:20px;color:#222;margin-top:18px}
.service-card p{font-size:12.5px;line-height:16px;color:var(--grey);margin-top:8px;padding:0 16px}
.service-card .more{position:absolute;left:90px;bottom:-18px;width:36px;height:36px;border-radius:50%;background:var(--green-dark);color:var(--white);font-weight:700;font-size:20px;line-height:34px;clip-path:inset(0 0 50% 0)}

/* team */
.team{top:2212px;height:647px;background:var(--white)}
.team .section-title{top:72px;color:var(--grey)}
.team-intro{position:absolute;left:195px;top:144px;width:810px;text-align:center;font-size:14px;line-height:22px;color:var(--grey)}
.member{position:absolute;top:265px;width:220px;text-align:center}
.member-photo{width:204px;height:204px;margin:0 auto;border-radius:50%;border:7px solid var(--green)}
.member-photo.tone-a{background:linear-gradient(180deg,#dfe5ea 0%,#b9c4cc 45%,#4a5562 70%,#2e3a4a 100%)}
.member-photo.tone-b{background:linear-gradient(180deg,#c7c9cf 0%,#8e7a6e 45%,#3b2e2a 75%,#22242c 100%)}
.member-photo.tone-c{background:linear-gradient(180deg,#e6eaee 0%,#c9b6a2 45%,#d9e4ee 72%,#2b4f8a 100%)}
.member-name{margin-top:18px;font-size:16px;color:var(--grey)}
.member-name b{color:var(--green);font-weight:600}
.member-social{display:flex;justify-content:center;gap:5px;margin-top:6px}
.member-social span{width:26px;height:26px;border-radius:50%;background:var(--green)}

/* products */
.products{top:2859px;height:645px;background:var(--dark)}
.products .section-title{top:68px;color:var(--white)}
.product{position:absolute;display:flex;align-items:center;gap:24px;width:440px}
.product-photo{flex:none;width:118px;height:118px;border-radius:50%;border:6px solid var(--white);box-shadow:0 0 0 4px var(--green)}
.p-solar{background:linear-gradient(150deg,#eef2f6 0%,#6d8cc0 35%,#1f3d7a 70%,#e9eef3 100%)}
.p-pfc{background:linear-gradient(160deg,#f2f2f2 0%,#9aa2ad 40%,#2d3a55 70%,#d8dde2 100%)}
.p-meter{background:radial-gradient(circle at 50% 50%,#f4f4f4 0%,#dadada 40%,#6b6b6b 75%,#e9e9e9 100%)}
.p-wind{background:linear-gradient(180deg,#6c9ed8 0%,#a9c8ec 45%,#f2f5f8 70%,#6c9ed8 100%)}
.p-gauge{background:radial-gradient(circle at 50% 50%,#ffffff 0%,#e6e6e6 45%,#8a8f94 70%,#f0f0f0 100%)}
.p-array{background:linear-gradient(120deg,#f3f5f7 0%,#2a3d6a 30%,#15244a 60%,#c8d0da 100%)}
.product h4{font-family:"Open Sans",sans-serif;font-weight:400;font-size:21px;color:var(--green-light)}
.product p{font-size:13px;line-height:17px;color:var(--white);margin-top:8px;width:260px}

/* footer */
.site-footer{top:3504px;height:318px;background:var(--footer);text-align:center;color:var(--white)}
.footer-address{margin-top:66px;font-weight:700;font-size:16px;line-height:26px}
.footer-social{display:flex;justify-content:center;gap:22px;margin-top:44px}
.footer-social span{width:12px;height:12px;background:var(--white);border-radius:50%}
.copyright{margin-top:46px;font-size:10px;opacity:.9}
</style>
</head>
<body>
<div class="page">

<header class="site-header">
  <div class="brand"><span class="brand-dot"></span><span class="brand-name">Tidal Forge</span></div>
  <div class="call">
    <div class="call-label">CALL US NOW</div>
    <div class="call-number">
      <svg width="26" height="26" viewBox="0 0 26 26"><circle cx="13" cy="13" r="13" fill="#2e9e44"/><path d="M9 7c1 0 2 3 2 3l-1.5 1.5c.8 2 2.5 3.7 4.5 4.5L15.5 14.5s3 1 3 2c0 1.5-1.5 2.5-2.5 2.5C11 19 7 15 7 10c0-1 1-3 2-3z" fill="#fff"/></svg>
      1-800-555-0142
    </div>
  </div>
  <div class="follow">
    <div class="follow-label">FOLLOW US</div>
    <div class="follow-icons"><span></span><span></span><span></span><span></span></div>
  </div>
  <nav class="main-nav">
    <a class="active" href="#"><span>Home</span></a>
    <a href="#">About</a>
    <a href="#">Team</a>
    <a href="#">Services</a>
    <a href="#">Products</a>
    <a href="#">Clients</a>
    <a href="#">Contact</a>
  </nav>
</header>

<section class="hero">
  <div class="hero-visual" role="img" aria-label="Solar panel field with power pylons and wind turbines at sunset"></div>
  <h1 class="hero-title">WITH US<br>MINING EQUIPMENT RUN<br>GREENER AND MORE EFFICIENT</h1>
  <svg class="hero-arrow" style="left:84px" width="18" height="34" viewBox="0 0 18 34"><path d="M16 2L2 17l14 15" fill="none" stroke="#fff" stroke-width="4"/></svg>
  <svg class="hero-arrow" style="left:1098px" width="18" height="34" viewBox="0 0 18 34"><path d="M2 2l14 15L2 32" fill="none" stroke="#fff" stroke-width="4"/></svg>
</section>

<section class="about">
  <h2 class="section-title"><svg width="28" height="30" viewBox="0 0 28 30"><path d="M4 28C2 14 10 4 26 2c0 14-8 24-22 26z" fill="#2e9e44"/></svg>About us</h2>
  <div class="about-photo" role="img" aria-label="Mining rig housing facility lit at night"></div>
  <div class="about-text">
    <p>Lorem ipsum dolor sit amet, pro everti deseruisse et, tota nostrud ei pro. Eu dicam molestie intellegat vim, mei eu mutat malorum lucilius. Legere detraxit scriptorem cum ex, sale viris nam id. Vel et consulatu gloriatur, per no fabulas molestiae suscipiantur. At eam odio putant, solum adolescens in mei.</p>
    <p>Ei ius falli facilisis. Ubique voluptua te cum, vix inermis pertinacia an, vix ad mentitum persecuti. Est veritus facilisi dissentiet cu.</p>
  </div>
  <div class="read-more">READ MORE <i><svg width="12" height="12" viewBox="0 0 12 12"><path d="M4 2l4 4-4 4" fill="none" stroke="#2e9e44" stroke-width="2"/></svg></i></div>
</section>

<section class="services">
  <h2 class="section-title"><svg width="28" height="30" viewBox="0 0 28 30"><path d="M4 28C2 14 10 4 26 2c0 14-8 24-22 26z" fill="#fff"/></svg>Our services</h2>

  <div class="service-card" style="left:138px;top:163px"><div class="service-icon"><svg viewBox="0 0 74 74"><circle cx="37" cy="37" r="37" fill="#2e9e44"/><path d="M37 18a13 13 0 0 0-8 23c2 2 3 4 3 6h10c0-2 1-4 3-6a13 13 0 0 0-8-23z" fill="none" stroke="#fff" stroke-width="3"/><path d="M32 51h10M33 56h8" stroke="#fff" stroke-width="3" stroke-linecap="round"/></svg></div><h3>CONSECTETUR ADIPI<br>SCING ELIT</h3><p>Lorem ipsum dolor sit amet, consectetur adipiscing elit. Lorem ipsum dolor sit amet, consectetur adipiscing elit.</p><div class="more">+</div></div>

  <div class="service-card" style="left:375px;top:163px"><div class="service-icon"><svg viewBox="0 0 74 74"><circle cx="37" cy="37" r="37" fill="#2e9e44"/><g stroke="#fff" stroke-width="6" stroke-linecap="round"><path d="M37 16v7M37 51v7M16 37h7M51 37h7M22 22l5 5M47 47l5 5M52 22l-5 5M27 47l-5 5"/></g><circle cx="37" cy="37" r="12" fill="none" stroke="#fff" stroke-width="4"/><circle cx="37" cy="37" r="4" fill="#fff"/></svg></div><h3>CONSECTETUR ADIPI<br>SCING ELIT</h3><p>Lorem ipsum dolor sit amet, consectetur adipiscing elit. Lorem ipsum dolor sit amet, consectetur adipiscing elit.</p><div class="more">+</div></div>

  <div class="service-card" style="left:607px;top:163px"><div class="service-icon"><svg viewBox="0 0 74 74"><circle cx="37" cy="37" r="37" fill="#2e9e44"/><path d="M35 32h4l2 28h-8z" fill="#fff"/><g fill="#fff"><path d="M37 30l-3-16 6 0z"/><path d="M37 30l14 9-3 5z"/><path d="M37 30l-14 9 3 5z"/></g><circle cx="37" cy="30" r="3" fill="#2e9e44" stroke="#fff" stroke-width="2"/></svg></div><h3>CONSECTETUR ADIPI<br>SCING ELIT</h3><p>Lorem ipsum dolor sit amet, consectetur adipiscing elit. Lorem ipsum dolor sit amet, consectetur adipiscing elit.</p><div class="more">+</div></div>

  <div class="service-card" style="left:843px;top:163px"><div class="service-icon"><svg viewBox="0 0 74 74"><circle cx="37" cy="37" r="37" fill="#2e9e44"/><path d="M18 54V36l10 6v-6l10 6v-6l10 6V22h6v32z" fill="#fff"/><rect x="24" y="47" width="5" height="4" fill="#2e9e44"/><rect x="33" y="47" width="5" height="4" fill="#2e9e44"/><rect x="42" y="47" width="5" height="4" fill="#2e9e44"/></svg></div><h3>CONSECTETUR ADIPI<br>SCING ELIT</h3><p>Lorem ipsum dolor sit amet, consectetur adipiscing elit. Lorem ipsum dolor sit amet, consectetur adipiscing elit.</p><div class="more">+</div></div>

  <div class="service-card" style="left:138px;top:454px"><div class="service-icon"><svg viewBox="0 0 74 74"><circle cx="37" cy="37" r="37" fill="#2e9e44"/><g fill="none" stroke="#fff" stroke-width="3.5" stroke-linecap="round"><path d="M27 18h20M27 24h20M27 30h20M27 36h20"/><path d="M27 18c-4 0-4 6 0 6M27 24c-4 0-4 6 0 6M27 30c-4 0-4 6 0 6M47 18c4 0 4 6 0 6M47 24c4 0 4 6 0 6M47 30c4 0 4 6 0 6"/></g><path d="M30 41h14l-2 12H32z" fill="#fff"/><rect x="34" y="54" width="6" height="4" fill="#fff"/></svg></div><h3>CONSECTETUR ADIPI<br>SCING ELIT</h3><p>Lorem ipsum dolor sit amet, consectetur adipiscing elit. Lorem ipsum dolor sit amet, consectetur adipiscing elit.</p><div class="more">+</div></div>

  <div class="service-card" style="left:375px;top:454px"><div class="service-icon"><svg viewBox="0 0 74 74"><circle cx="37" cy="37" r="37" fill="#2e9e44"/><circle cx="37" cy="37" r="18" fill="none" stroke="#fff" stroke-width="3"/><path d="M33 28v6M41 28v6" stroke="#fff" stroke-width="3" stroke-linecap="round"/><path d="M29 34h16v4a8 8 0 0 1-16 0z" fill="#fff"/><path d="M37 46v6" stroke="#fff" stroke-width="3"/></svg></div><h3>CONSECTETUR ADIPI<br>SCING ELIT</h3><p>Lorem ipsum dolor sit amet, consectetur adipiscing elit. Lorem ipsum dolor sit amet, consectetur adipiscing elit.</p><div class="more">+</div></div>

  <div class="service-card" style="left:607px;top:454px"><div class="service-icon"><svg viewBox="0 0 74 74"><circle cx="37" cy="37" r="37" fill="#2e9e44"/><path d="M37 16c-6 9-9 14-9 18a9 9 0 0 0 18 0c0-4-3-9-9-18z" fill="#fff"/><path d="M16 50c6 0 10-3 15-3h10c2 0 2 4 0 4h-8M44 50l10-5c2-1 4 1 2 3l-11 7H16" fill="none" stroke="#fff" stroke-width="3" stroke-linejoin="round"/></svg></div><h3>CONSECTETUR ADIPI<br>SCING ELIT</h3><p>Lorem ipsum dolor sit amet, consectetur adipiscing elit. Lorem ipsum dolor sit amet, consectetur adipiscing elit.</p><div class="more">+</div></div>

  <div class="service-card" style="left:843px;top:454px"><div class="service-icon"><svg viewBox="0 0 74 74"><circle cx="37" cy="37" r="37" fill="#2e9e44"/><circle cx="37" cy="37" r="19" fill="none" stroke="#fff" stroke-width="3"/><ellipse cx="37" cy="37" rx="8" ry="19" fill="none" stroke="#fff" stroke-width="3"/><path d="M18 37h38M21 28h32M21 46h32" stroke="#fff" stroke-width="3"/></svg></div><h3>CONSECTETUR ADIPI<br>SCING ELIT</h3><p>Lorem ipsum dolor sit amet, consectetur adipiscing elit. Lorem ipsum dolor sit amet, consectetur adipiscing elit.</p><div class="more">+</div></div>
</section>

<section class="team">
  <h2 class="section-title"><svg width="28" height="30" viewBox="0 0 28 30"><path d="M4 28C2 14 10 4 26 2c0 14-8 24-22 26z" fill="#2e9e44"/></svg>Our Team</h2>
  <p class="team-intro">Lorem ipsum dolor sit amet, consectetur adipiscing elit. Nihil enim hoc differt. Invidiosum nomen est, infame, suspectum. Habent enim et bene longam et satis litigiosam disputationem. Vitae autem degendae ratio maxime quidem illis placuit queta. Illum mallem levares, quo optimum atque</p>
  <div class="member" style="left:183px"><div class="member-photo tone-a" role="img" aria-label="Portrait of Evan Marsh, CEO"></div><div class="member-name"><b>Evan Marsh</b>, CEO</div><div class="member-social"><span></span><span></span><span></span><span></span></div></div>
  <div class="member" style="left:504px"><div class="member-photo tone-b" role="img" aria-label="Portrait of Lina, Manager"></div><div class="member-name"><b>Lina</b>, Manager</div><div class="member-social"><span></span><span></span><span></span><span></span></div></div>
  <div class="member" style="left:825px"><div class="member-photo tone-c" role="img" aria-label="Portrait of Rafe Colton, CEO"></div><div class="member-name"><b>Rafe Colton</b>, CEO</div><div class="member-social"><span></span><span></span><span></span><span></span></div></div>
</section>

<section class="products">
  <h2 class="section-title"><svg width="28" height="30" viewBox="0 0 28 30"><path d="M4 28C2 14 10 4 26 2c0 14-8 24-22 26z" fill="#2e9e44"/></svg>Our Products</h2>
  <div class="product" style="left:158px;top:168px"><div class="product-photo p-solar" role="img" aria-label="Solar panel"></div><div><h4>Omnesque accusamus</h4><p>Lorem ipsum dolor sit amet, id imperdiet intellegebat his, soluta legimus sententiae et per.</p></div></div>
  <div class="product" style="left:637px;top:160px"><div class="product-photo p-pfc" role="img" aria-label="Power factor correction unit"></div><div><h4>Omnesque accusamus</h4><p>Lorem ipsum dolor sit amet, id imperdiet intellegebat his, soluta legimus sententiae et per.</p></div></div>
  <div class="product" style="left:158px;top:305px"><div class="product-photo p-meter" role="img" aria-label="Power meter"></div><div><h4>Omnesque accusamus</h4><p>Lorem ipsum dolor sit amet, id imperdiet intellegebat his, soluta legimus sententiae et per.</p></div></div>
  <div class="product" style="left:637px;top:305px"><div class="product-photo p-wind" role="img" aria-label="Wind turbine"></div><div><h4>Omnesque accusamus</h4><p>Lorem ipsum dolor sit amet, id imperdiet intellegebat his, soluta legimus sententiae et per.</p></div></div>
  <div class="product" style="left:158px;top:451px"><div class="product-photo p-gauge" role="img" aria-label="Energy gauge"></div><div><h4>Omnesque accusamus</h4><p>Lorem ipsum dolor sit amet, id imperdiet intellegebat his, soluta legimus sententiae et per.</p></div></div>
  <div class="product" style="left:637px;top:451px"><div class="product-photo p-array" role="img" aria-label="Solar panel array"></div><div><h4>Omnesque accusamus</h4><p>Lorem ipsum dolor sit amet, id imperdiet intellegebat his, soluta legimus sententiae et per.</p></div></div>
</section>

<footer class="site-footer">
  <div class="footer-address">2261 Cedarline Way, Fairbanks, Alaska 99709<br>Phone (555) 014 7720</div>
  <div class="footer-social"><span></span><span></span><span></span><span></span></div>
  <div class="copyright">© 2017 All rights reserved by Tidal Forge</div>
</footer>

</div>
</body>
</html>
```